Meridale Bed Company Needs Business Card

Looking for a very nice looking business card. Creative but not extravagant. We sell beds and pillows across the U.S. and need something professional but catchy. I have attached the logo.

Name : Devin Holt
Title : President
Phone : (800) 471-2960
Email: sleep@quilmora.com
Website: www.quilmora.com

Can be single-sided or double-sided
horizontal or vertical

Can use Blues/Greys

Target Market(s)

Mass Market

Industry/Entity Type

Retail

Contact Information for Business Card

Name : Devin Holt
Title : President
Phone : (800) 471-2960
Email: sleep@quilmora.com
Website: www.quilmora.com

Requirements
Must have
• Clean, Modern, Smooth
• Can use Blues/Greys
• On the other side without the information - have something simple like www.quilmora.com or our logo
Nice to have
• Surprise me
Should not have
• Nothing crazy, nothing cluttered

```html
<!DOCTYPE html>
<html lang="en">
<head>
<meta charset="utf-8">
<title>Meridale Bed Company — Business Card</title>
<link rel="stylesheet" href="https://fonts.googleapis.com/css2?family=Open+Sans:wght@400;700&display=swap">
<style>
  :root {
    --page-bg: #e6e6e4;
    --card-black: #050505;
    --card-black-soft: #141414;
    --brand-blue: #2ea6dc;
    --text-white: #ffffff;
    --text-muted: #e8e8e8;
  }
  * { margin: 0; padding: 0; box-sizing: border-box; }
  html, body {
    width: 1200px;
    height: 900px;
    overflow: hidden;
    background: var(--page-bg);
  }
  .canvas {
    position: relative;
    width: 1200px;
    height: 900px;
  }
  .card {
    position: absolute;
    width: 540px;
    height: 310px;
    background: var(--card-black);
    box-shadow: 0 6px 18px rgba(0, 0, 0, 0.25);
    overflow: hidden;
    font-family: "Open Sans", sans-serif;
  }

  /* Back side */
  .card--back { left: 70px; top: 150px; }
  .back-texture {
    position: absolute;
    inset: 0;
    background: radial-gradient(ellipse at 40% 60%, var(--card-black-soft) 0%, var(--card-black) 75%);
  }
  .back-wordmark {
    position: absolute;
    left: 0; right: 0;
    top: 100px;
    text-align: center;
    font-weight: 400;
    font-size: 60px;
    color: var(--text-white);
    line-height: 1;
  }
  .back-url {
    position: absolute;
    left: 0; right: 0;
    top: 208px;
    text-align: center;
    font-weight: 700;
    font-size: 13px;
    color: var(--text-white);
  }

  /* Front side */
  .card--front { left: 590px; top: 440px; }
  .front-wordmark {
    position: absolute;
    left: 0; right: 0;
    top: 44px;
    text-align: center;
    font-weight: 400;
    font-size: 56px;
    color: var(--brand-blue);
    line-height: 1;
  }
  .divider {
    position: absolute;
    left: 0; right: 0;
    top: 140px;
    height: 2px;
    background: var(--brand-blue);
  }
  .contact-list {
    position: absolute;
    right: 16px;
    top: 156px;
    list-style: none;
    font-size: 12px;
    color: var(--text-muted);
    text-align: right;
  }
  .contact-list li {
    display: flex;
    justify-content: flex-end;
    align-items: center;
    gap: 6px;
    line-height: 19px;
  }
  .contact-icon { width: 10px; height: 10px; flex: none; }
  .person {
    position: absolute;
    left: 40px;
    top: 184px;
  }
  .person-name {
    font-weight: 700;
    font-size: 21px;
    color: var(--brand-blue);
    line-height: 1.1;
  }
  .person-title {
    font-weight: 400;
    font-size: 15px;
    color: var(--text-white);
    margin-left: 14px;
    line-height: 1.3;
  }
</style>
</head>
<body>
<main class="canvas">

  <section class="card card--back" aria-label="Business card, back">
    <div class="back-texture" role="img" aria-label="Faint repeated brand name texture in dark grey"></div>
    <div class="back-wordmark">quilmora</div>
    <div class="back-url">www.quilmora.com</div>
  </section>

  <section class="card card--front" aria-label="Business card, front">
    <div class="front-wordmark">quilmora</div>

    <div class="divider"></div>

    <ul class="contact-list">
      <li>(800) 471-2960
        <svg class="contact-icon" viewBox="0 0 10 10" aria-hidden="true">
          <path d="M1 4.2 Q5 1.5 9 4.2 L8 5.4 L6.6 4.6 L6.6 3.8 Q5 3.3 3.4 3.8 L3.4 4.6 L2 5.4 Z M2.5 6 H7.5 L8 8.5 H2 Z" fill="var(--brand-blue)"/>
        </svg>
      </li>
      <li>sleep@quilmora.com
        <svg class="contact-icon" viewBox="0 0 10 10" aria-hidden="true">
          <rect x="0.5" y="2" width="9" height="6.5" fill="var(--brand-blue)"/>
          <path d="M0.8 2.3 L5 5.6 L9.2 2.3" stroke="var(--card-black)" stroke-width="0.9" fill="none"/>
        </svg>
      </li>
      <li>www.quilmora.com
        <svg class="contact-icon" viewBox="0 0 10 10" aria-hidden="true">
          <circle cx="5" cy="5" r="4.5" fill="var(--brand-blue)"/>
          <ellipse cx="5" cy="5" rx="1.8" ry="4.5" stroke="var(--card-black)" stroke-width="0.7" fill="none"/>
          <line x1="0.5" y1="5" x2="9.5" y2="5" stroke="var(--card-black)" stroke-width="0.7"/>
        </svg>
      </li>
    </ul>

    <div class="person">
      <div class="person-name">Devin Holt</div>
      <div class="person-title">President</div>
    </div>
  </section>

</main>
</body>
</html>
```